Vantro cards

I am in the auto motive, transportation business I would like a business card that is Something cool, modern edgy, having to do with car culture. I offer towing service for high and exotic cars. I also provide towing for collisions and car accidents. I offer open and enclosed transport nationwide.

Target Market(s)

Car culture people high end auto collectors

Industry/Entity Type

Towing car carrier

Contact Information for Business Card

My company colors black yellow and silver

Font styles to use
Serif

```html
<!DOCTYPE html>
<html lang="en">
<head>
<meta charset="utf-8">
<title>Vantro Transportation – Business Cards</title>
<link href="https://fonts.googleapis.com/css2?family=Montserrat:wght@500;600;800&display=swap" rel="stylesheet">
<style>
  :root {
    --ink: #050505;
    --card-white: #ffffff;
    --card-off: #f3f3f3;
    --brand-yellow: #f0bf2c;
    --brand-silver: #cfcfcf;
    --canvas-bg: #d6d6d6;
  }
  * { box-sizing: border-box; margin: 0; padding: 0; }
  html, body {
    width: 1200px; height: 1200px; overflow: hidden;
    background: var(--canvas-bg);
    font-family: "Montserrat", Arial, sans-serif;
  }
  .card {
    position: absolute;
    left: 150px;
    width: 900px; height: 514px;
    border-radius: 30px;
    overflow: hidden;
    box-shadow: 0 10px 30px rgba(0,0,0,.25);
  }
  .card--front {
    top: 60px;
    background: linear-gradient(180deg, var(--card-white), var(--card-off));
  }
  .card--back {
    top: 626px;
    background: var(--ink);
  }
  .front-shapes { position: absolute; inset: 0; }

  .contact-block {
    position: absolute;
    left: 92px; top: 250px;
    color: var(--card-white);
  }
  .name-row {
    position: relative;
    padding-left: 20px;
  }
  .name-row::before {
    content: "";
    position: absolute; left: 0; top: 4px;
    width: 6px; height: 52px;
    background: var(--brand-yellow);
  }
  .person-name {
    font-weight: 600;
    font-size: 36px;
    line-height: 1;
    letter-spacing: 1px;
    color: var(--brand-yellow);
  }
  .person-role {
    font-weight: 500;
    font-size: 15px;
    letter-spacing: 1px;
    margin-top: 3px;
  }
  .contact-list { list-style: none; margin-top: 20px; }
  .contact-item {
    display: flex; align-items: center; gap: 12px;
    font-size: 21px; font-weight: 500;
    letter-spacing: .4px;
    margin-bottom: 9px;
  }
  .contact-icon { width: 24px; height: 24px; flex: none; }

  .wordmark {
    position: absolute;
    display: flex; align-items: center; gap: 14px;
    font-weight: 800;
    letter-spacing: 3px;
    line-height: 1;
  }
  .wordmark__mark { flex: none; background: var(--brand-yellow); }
  .wordmark--front {
    left: 612px; top: 152px;
    font-size: 42px; color: var(--ink);
  }
  .wordmark--front .wordmark__mark { width: 22px; height: 22px; }

  .back-glow {
    position: absolute; inset: 0;
    background: radial-gradient(circle at 50% 48%, #3a3a3a 0%, #1a1a1a 38%, #070707 75%);
  }
  .wordmark--back {
    left: 50%; top: 50%;
    transform: translate(-50%, -50%);
    font-size: 96px; color: var(--brand-yellow);
  }
  .wordmark--back .wordmark__mark { width: 44px; height: 44px; }
</style>
</head>
<body>

<section class="card card--front" aria-label="Business card front">
  <svg class="front-shapes" viewBox="0 0 900 514" width="900" height="514" aria-hidden="true">
    <polygon points="0,0 260,0 530,250 410,514 0,514" fill="var(--ink)"/>
    <polyline points="292,-6 564,250 442,520" fill="none" stroke="var(--brand-yellow)" stroke-width="10" stroke-linejoin="miter"/>
  </svg>

  <div class="contact-block">
    <div class="name-row">
      <h1 class="person-name">JOHN DOE</h1>
      <p class="person-role">POSITION</p>
    </div>
    <ul class="contact-list">
      <li class="contact-item">
        <svg class="contact-icon" viewBox="0 0 24 24"><path fill="var(--brand-yellow)" d="M6.6 10.8a15.1 15.1 0 0 0 6.6 6.6l2.2-2.2a1 1 0 0 1 1-.25 11.4 11.4 0 0 0 3.6.57 1 1 0 0 1 1 1V20a1 1 0 0 1-1 1A17 17 0 0 1 3 4a1 1 0 0 1 1-1h3.5a1 1 0 0 1 1 1c0 1.250.2 2.45.57 3.57a1 1 0 0 1-.25 1z"/></svg>
        <span>(000) 000 0000</span>
      </li>
      <li class="contact-item">
        <svg class="contact-icon" viewBox="0 0 24 24"><rect x="2" y="5" width="20" height="14" fill="var(--brand-yellow)"/><path d="M2 5l10 8 10-8" fill="none" stroke="var(--ink)" stroke-width="1.6"/></svg>
        <span>email@youremail.com</span>
      </li>
      <li class="contact-item">
        <svg class="contact-icon" viewBox="0 0 24 24" fill="none" stroke="var(--brand-yellow)" stroke-width="1.8"><circle cx="12" cy="12" r="10"/><ellipse cx="12" cy="12" rx="4.5" ry="10"/><path d="M2 12h20M4 7h16M4 17h16"/></svg>
        <span>www.yourwebsite.com</span>
      </li>
    </ul>
  </div>

  <div class="wordmark wordmark--front">
    <span class="wordmark__mark"></span>
    <span class="wordmark__name">VANTRO</span>
  </div>
</section>

<section class="card card--back" aria-label="Business card back">
  <div class="back-glow" role="img" aria-label="Radiating grey light rays spreading out from behind the company name"></div>
  <div class="wordmark wordmark--back">
    <span class="wordmark__mark"></span>
    <span class="wordmark__name">VANTRO</span>
  </div>
</section>

</body>
</html>
```